ultra-minimalist business card

front (black background, matte):

reza t. kovin
writer | photographer
get@rezakovin.com

back (white background, matte):

a picture speaks a thousand words;
a word draws a thousand pictures.

www.rezakovin.com

all text should be small (white or silver - as long as it shows against the black - on the front; black or gray - as long as it shows against the white - on the back).

feel free to get creative in terms of arrangement, alignment, and font type, but remember, the overall style is minimalist, so nothing too fancy, please.

thanks.

```html
<!DOCTYPE html>
<html lang="en">
<head>
<meta charset="utf-8">
<title>reza t. kovin — business card</title>
<link rel="stylesheet" href="https://fonts.googleapis.com/css2?family=Archivo+Black&family=Roboto+Condensed:ital,wght@0,400;0,700;1,700&display=swap">
<style>
  :root {
    --canvas: #ffffff;
    --front-dark: #0b0c0e;
    --front-mid: #1a1c1f;
    --front-ink: #ffffff;
    --front-muted: #a3a6aa;
    --front-rule: #8d9196;
    --back-light: #ffffff;
    --back-tint: #e4ecee;
    --back-ink: #111111;
    --back-initial: #a3a3a3;
    --back-rule: #222222;
    --shadow: rgba(0, 0, 0, 0.28);
  }

  * { margin: 0; padding: 0; box-sizing: border-box; }

  html, body {
    width: 1000px;
    height: 1200px;
    overflow: hidden;
    background: var(--canvas);
  }

  .canvas {
    position: relative;
    width: 1000px;
    height: 1200px;
  }

  .card {
    position: absolute;
    left: 93px;
    width: 829px;
    overflow: hidden;
    box-shadow: -6px 10px 22px var(--shadow);
  }

  .card-texture {
    position: absolute;
    inset: 0;
    width: 100%;
    height: 100%;
  }

  /* front */
  .card--front {
    top: 85px;
    height: 474px;
  }

  .holder-name {
    position: absolute;
    left: 25px;
    top: 178px;
    font-family: "Archivo Black", "Arial Black", sans-serif;
    font-size: 70px;
    line-height: 1;
    letter-spacing: 1px;
    color: var(--front-ink);
    white-space: nowrap;
    transform: rotate(-6.5deg);
    transform-origin: 0 80%;
  }

  .holder-role {
    position: absolute;
    right: 22px;
    top: 206px;
    font-family: "Roboto Condensed", "Arial Narrow", sans-serif;
    font-size: 31px;
    font-weight: 400;
    color: var(--front-muted);
    white-space: nowrap;
  }

  .rule-row {
    position: absolute;
    left: 0;
    right: 0;
    display: flex;
    align-items: center;
    gap: 12px;
  }

  .rule-row::before,
  .rule-row::after {
    content: "";
    flex: 1;
    height: 2px;
  }

  .rule-row--front { top: 430px; }
  .rule-row--front::before,
  .rule-row--front::after { background: var(--front-rule); }

  .contact-email {
    font-family: "Roboto Condensed", "Arial Narrow", sans-serif;
    font-size: 24px;
    color: var(--front-muted);
    white-space: nowrap;
  }

  /* back */
  .card--back {
    top: 642px;
    height: 457px;
  }

  .initial {
    position: absolute;
    left: 40px;
    font-family: "Roboto Condensed", "Arial Narrow", sans-serif;
    font-weight: 700;
    font-size: 206px;
    line-height: 1;
    color: var(--back-initial);
  }

  .initial--one { top: -16px; }
  .initial--two { top: 148px; }

  .motto-line {
    position: absolute;
    left: 113px;
    font-family: "Roboto Condensed", "Arial Narrow", sans-serif;
    font-style: italic;
    font-weight: 700;
    font-size: 47px;
    line-height: 1;
    color: var(--back-ink);
    white-space: nowrap;
  }

  .motto-line--one { top: 131px; }
  .motto-line--two { top: 295px; }

  .rule-row--back { top: 414px; }
  .rule-row--back::before,
  .rule-row--back::after { background: var(--back-rule); }

  .contact-web {
    font-family: "Roboto Condensed", "Arial Narrow", sans-serif;
    font-weight: 700;
    font-size: 24px;
    color: var(--back-ink);
    white-space: nowrap;
  }
</style>
</head>
<body>
<main class="canvas">

  <section class="card card--front" aria-label="Card front">
    <svg class="card-texture" role="img" aria-label="Subtle dark geometric diamond texture" viewBox="0 0 829 474" preserveAspectRatio="none">
      <defs>
        <linearGradient id="front-shade" x1="0" y1="0" x2="0" y2="1">
          <stop offset="0" stop-color="var(--front-mid)"/>
          <stop offset="0.55" stop-color="var(--front-dark)"/>
          <stop offset="1" stop-color="var(--front-mid)"/>
        </linearGradient>
      </defs>
      <rect width="829" height="474" fill="url(#front-shade)"/>
    </svg>

    <h1 class="holder-name">reza t. kovin</h1>
    <p class="holder-role">writer • photographer</p>

    <div class="rule-row rule-row--front">
      <span class="contact-email">get@rezakovin.com</span>
    </div>
  </section>

  <section class="card card--back" aria-label="Card back">
    <svg class="card-texture" role="img" aria-label="Soft light geometric diamond texture" viewBox="0 0 829 457" preserveAspectRatio="none">
      <defs>
        <linearGradient id="back-shade" x1="0" y1="0" x2="0" y2="1">
          <stop offset="0" stop-color="var(--back-light)"/>
          <stop offset="0.6" stop-color="var(--back-tint)"/>
          <stop offset="1" stop-color="var(--back-light)"/>
        </linearGradient>
      </defs>
      <rect width="829" height="457" fill="url(#back-shade)"/>
    </svg>

    <span class="initial initial--one" aria-hidden="true">A</span>
    <span class="initial initial--two" aria-hidden="true">A</span>

    <p class="motto-line motto-line--one"><span class="sr-initial" hidden>a </span>picture speaks a thousand words;</p>
    <p class="motto-line motto-line--two"><span class="sr-initial" hidden>a </span>word draws a thousand pictures.</p>

    <div class="rule-row rule-row--back">
      <span class="contact-web">www.rezakovin.com</span>
    </div>
  </section>

</main>
</body>
</html>
```